Bright Path Mentors Needs A New Website Design

We need a 8 page website designed for "Bright Path Mentors .ca" similar in design to: "keystone learning hub .com".

The winner/successful candidate on the home page will be asked to complete the following inner pages to complete the project:

About Us
Philosophy
How We Work
Work With Us
Blog
Find A Tutor
Contact

Target Market(s)

Tutoring business clients/children

Industry/Entity Type

Education

Number of Pages Required

5+ page

Font styles to use
Sans Serif

Requirements
Must have
• The attached logo included of course. Similar design to the design provided above in the brief. Clear high quality high resolution images of children in school settings.

```html
<!DOCTYPE html>
<html lang="en">
<head>
<meta charset="utf-8">
<title>Bright Path Mentors</title>
<link href="https://fonts.googleapis.com/css2?family=Open+Sans:wght@400;600&family=Roboto+Condensed:wght@400;700&display=swap" rel="stylesheet">
<style>
:root{
  --blue:#2f3c9e;
  --blue-deep:#26328a;
  --orange:#f7941d;
  --orange-dark:#e07f10;
  --green:#7dbb3a;
  --ink:#333;
  --muted:#777;
  --light:#f4f4f4;
  --paper:#fbf8f1;
  --dark:#222;
  --white:#fff;
}
*{box-sizing:border-box;margin:0;padding:0}
html,body{width:1200px;height:2839px;overflow:hidden;background:var(--white)}
body{position:relative;font-family:"Open Sans",Arial,sans-serif;color:var(--ink)}
.abs{position:absolute}
.cond{font-family:"Roboto Condensed","Arial Narrow",sans-serif}

/* header */
.brand{left:96px;top:40px;display:flex;align-items:center;gap:12px}
.brand-dot{width:44px;height:44px;border-radius:50%;background:var(--orange)}
.brand-name{font-family:"Roboto Condensed",sans-serif;font-weight:700;font-size:26px;color:var(--blue);line-height:1.05;width:130px}
.contact-top{left:575px;top:38px;font-size:15px;color:var(--ink);line-height:1.55}
.contact-top .call{color:var(--blue);font-family:"Roboto Condensed",sans-serif}
.phone-ring{left:573px;top:44px;width:34px;height:34px;border:1px solid #999;border-radius:50%}
.contact-top{padding-left:42px;left:573px}
.btn-book{left:830px;top:40px;width:115px;height:36px;background:var(--orange);color:#fff;font-family:"Roboto Condensed",sans-serif;font-size:14px;display:flex;align-items:center;justify-content:center;border-radius:2px}
.social-top{left:965px;top:41px;display:flex;gap:6px}
.social-top span{width:32px;height:32px;border:1px solid #999;border-radius:50%}

.nav{left:265px;top:122px;width:935px;height:50px;background:var(--blue);display:flex;align-items:center}
.nav a{color:#fff;text-decoration:none;font-family:"Roboto Condensed",sans-serif;font-size:14px;padding:0 20px;height:100%;display:flex;align-items:center}
.nav a.active{background:var(--orange)}

/* hero */
.hero{left:0;top:172px;width:1200px;height:558px;background:linear-gradient(90deg,#d9e1e6 0%,#eef1f2 45%,#e4eaee 100%)}
.hero-title{left:735px;top:362px;font-family:"Roboto Condensed",sans-serif;font-weight:700;font-size:42px;color:var(--blue)}
.hero-sub{left:736px;top:420px;font-family:"Roboto Condensed",sans-serif;font-size:17px;color:#333;line-height:1.45}
.hero-btn{left:736px;top:480px;width:152px;height:42px;background:var(--orange);color:#fff;font-family:"Roboto Condensed",sans-serif;font-size:16px;display:flex;align-items:center;justify-content:center}
.arrow{top:425px;font-size:48px;color:rgba(255,255,255,.8);font-family:"Roboto Condensed",sans-serif}

.promo{left:0;top:728px;width:1200px;height:190px}
.promo-text{left:0;top:768px;width:1200px;text-align:center;font-family:"Roboto Condensed",sans-serif;font-size:30px;color:#fff}
.promo-btn{left:522px;top:825px;width:156px;height:40px;border:2px solid #fff;color:#fff;font-family:"Roboto Condensed",sans-serif;font-size:16px;display:flex;align-items:center;justify-content:center;border-radius:2px}

/* ribbon headings */
.ribbon{width:240px;height:60px;left:480px}
.ribbon-label{left:480px;width:240px;text-align:center;font-family:"Roboto Condensed",sans-serif;font-size:26px;color:#fff}

/* tutor cards */
.card{top:1083px;width:240px;height:288px;background:var(--paper);box-shadow:0 3px 8px rgba(0,0,0,.15);text-align:center}
.card-icon{position:absolute;left:75px;top:32px;width:90px;height:90px;border-radius:50%}
.card h3{position:absolute;top:136px;left:0;width:100%;font-family:"Roboto Condensed",sans-serif;font-weight:400;font-size:19px;color:#333}
.card p{position:absolute;top:170px;left:22px;width:196px;font-size:11.5px;line-height:1.65;color:var(--muted)}
.card .more{position:absolute;top:252px;left:40px;width:160px;border-top:1px solid #ddd;padding-top:8px;font-size:11px;color:#999}

/* welcome */
.welcome{left:0;top:1435px;width:1200px;height:473px;background:var(--blue)}
.welcome h2{position:absolute;left:98px;top:95px;font-family:"Roboto Condensed",sans-serif;font-weight:700;font-size:34px;color:#fff}
.welcome p{position:absolute;left:98px;width:490px;font-size:11.5px;line-height:1.75;color:#e6e8f5}
.welcome .btn{position:absolute;left:98px;top:325px;width:134px;height:38px;background:var(--orange);color:#fff;font-family:"Roboto Condensed",sans-serif;font-size:14px;display:flex;align-items:center;justify-content:center;border-radius:2px}
.video{position:absolute;left:618px;top:83px;width:482px;height:312px;background:#fff;padding:8px}
.video-art{width:466px;height:268px;background:linear-gradient(180deg,#eef0f2,#dfe3e6)}
.video-bar{position:absolute;left:8px;bottom:8px;width:466px;height:22px;background:#f0f0f0;display:flex;align-items:center;font-size:9px;color:#555;gap:10px;padding:0 10px}

/* blog */
.post{top:2048px;width:310px}
.post-img{width:310px;height:172px}
.post h4{margin-top:18px;font-weight:400;font-size:15px;color:#333}
.post .meta{margin-top:8px;font-size:12px;color:#555}
.post p{margin-top:12px;font-size:11.5px;line-height:1.75;color:#555;padding-bottom:14px;border-bottom:1px solid #e4e4e4}

/* guarantee */
.guarantee{left:0;top:2410px;width:1200px;height:105px;background:var(--green)}
.seal{left:103px;top:2386px;width:140px;height:140px;border-radius:50%;background:radial-gradient(circle,#f2c94c 0 55%,#caa02a 56% 62%,#222 63% 100%)}
.g-big{left:268px;top:2428px;font-family:"Roboto Condensed",sans-serif;font-size:30px;color:#fff}
.g-small{left:268px;top:2466px;font-family:"Roboto Condensed",sans-serif;font-size:19px;color:#fff;letter-spacing:.5px}
.sub-input{left:575px;top:2443px;width:420px;height:40px;background:#fff;border-radius:20px 0 0 20px;font-size:12px;color:#666;padding:12px 0 0 24px}
.sub-btn{left:950px;top:2443px;width:125px;height:40px;background:#2b2b2b;border-radius:20px;color:#fff;font-size:12px;display:flex;align-items:center;justify-content:center;font-weight:600}

/* footer */
.footer{left:0;top:2515px;width:1200px;height:265px;background:var(--light)}
.f-title{font-family:"Roboto Condensed",sans-serif;font-size:17px;color:#333;top:2567px}
.links{left:97px;top:2605px;list-style:none;font-size:11px;color:#666;line-height:21px}
.links li::before{content:"›";margin-right:10px;color:#999}
.f-contact{left:288px;font-size:12.5px;color:#555;line-height:1.6;padding-left:26px}
.f-contact .ico{position:absolute;left:0;top:3px;width:12px;height:12px}
.tweet{left:565px;width:285px;font-size:11px;color:#555;line-height:1.7;padding-left:26px}
.tweet b{color:var(--blue);font-weight:400}
.tweet .ico{position:absolute;left:0;top:4px;width:16px;height:14px;background:#444;border-radius:2px}
.f-brand{left:935px;top:2610px;display:flex;align-items:center;gap:12px}

.bottom{left:0;top:2780px;width:1200px;height:59px;background:var(--dark)}
.bottom p{position:absolute;left:104px;top:22px;font-size:11px;color:#bbb}
.bottom .soc{position:absolute;left:985px;top:17px;display:flex;gap:8px}
.bottom .soc span{width:24px;height:24px;border-radius:50%;background:#e5e5e5}
</style>
</head>
<body>

<!-- header -->
<div class="abs brand"><span class="brand-dot"></span><span class="brand-name">Bright Path Mentors</span></div>
<span class="abs phone-ring"></span>
<svg class="abs" style="left:582px;top:53px" width="16" height="16" viewBox="0 0 16 16"><path d="M3 1l3 3-2 2c1 2 3 4 5 5l2-2 3 3-2 3C6 15 1 10 1 3z" fill="#555"/></svg>
<div class="abs contact-top"><div class="call">CALL: +1 555 014 2290</div><div>info@brightpathmentors.ca</div></div>
<div class="abs btn-book">BOOKING NOW</div>
<div class="abs social-top"><span></span><span></span><span></span><span></span></div>

<nav class="abs nav">
  <a class="active" href="#">HOME</a><a href="#">ABOUT US</a><a href="#">PHILOSOPHY</a><a href="#">HOW WE WORK</a><a href="#">WORK WITH US</a><a href="#">BLOG</a><a href="#">FIND A TUTOR</a><a href="#">CONTACT</a>
</nav>

<!-- hero -->
<div class="abs hero" role="img" aria-label="Photo of a smiling tutor helping a young boy write at a bright classroom desk"></div>
<div class="abs arrow" style="left:30px">‹</div>
<div class="abs arrow" style="left:1135px">›</div>
<div class="abs hero-title">BRIGHT PATH MENTORS</div>
<div class="abs hero-sub">ALL SUBJECTS, ALL GRADES AVAILABLE ON-CALL<br>WHEN YOU NEED US MOST</div>
<div class="abs hero-btn">GET MORE INFO</div>

<svg class="abs promo" viewBox="0 0 1200 190" preserveAspectRatio="none">
  <polygon points="0,0 1200,0 1200,132 600,187 0,132" fill="#5a5a5a"/>
  <polygon points="0,0 1200,0 1200,127 600,182 0,127" fill="var(--orange)"/>
</svg>
<div class="abs promo-text">FIRST SESSION JUST $7! ALL SUBJECTS! ALL GRADES!</div>
<div class="abs promo-btn">BOOKING NOW</div>

<!-- our tutors -->
<svg class="abs ribbon" style="top:986px" viewBox="0 0 240 60">
  <polygon points="0,6 34,6 34,40 0,40 12,23" fill="var(--blue)"/>
  <polygon points="240,6 206,6 206,40 240,40 228,23" fill="var(--blue)"/>
  <rect x="24" y="12" width="192" height="40" fill="var(--orange)"/>
</svg>
<div class="abs ribbon-label" style="top:1003px">OUR TUTORS</div>

<div class="abs card" style="left:100px">
  <span class="card-icon" style="background:#1ea0dc"></span>
  <svg class="abs" style="left:100px;top:58px" width="40" height="38" viewBox="0 0 40 38"><rect x="2" y="2" width="36" height="24" rx="2" fill="none" stroke="#fff" stroke-width="3"/><rect x="14" y="30" width="12" height="4" fill="#fff"/></svg>
  <h3>Math Tutoring</h3>
  <p>Sed ut perspiciatis unde omnis iste natus error sit voluptatem accusantium doloremque laudantium.</p>
  <div class="more">READ MORE INFO</div>
</div>
<div class="abs card" style="left:357px">
  <span class="card-icon" style="background:#ef5a24"></span>
  <svg class="abs" style="left:100px;top:58px" width="40" height="38" viewBox="0 0 40 38"><rect x="4" y="2" width="32" height="22" rx="2" fill="none" stroke="#fff" stroke-width="3"/><rect x="0" y="28" width="40" height="5" rx="2" fill="#fff"/></svg>
  <h3>Science Tutoring</h3>
  <p>Sed ut perspiciatis unde omnis iste natus error sit voluptatem accusantium doloremque laudantium.</p>
  <div class="more">READ MORE INFO</div>
</div>
<div class="abs card" style="left:608px">
  <span class="card-icon" style="background:#7dbb3a"></span>
  <svg class="abs" style="left:100px;top:60px" width="40" height="34" viewBox="0 0 40 34"><path d="M20 6C14 2 7 2 2 4v26c5-2 12-2 18 2 6-4 13-4 18-2V4C33 2 26 2 20 6z" fill="none" stroke="#fff" stroke-width="3"/><line x1="20" y1="6" x2="20" y2="32" stroke="#fff" stroke-width="3"/></svg>
  <h3>Foreign Languages</h3>
  <p>Sed ut perspiciatis unde omnis iste natus error sit voluptatem accusantium doloremque laudantium.</p>
  <div class="more">READ MORE INFO</div>
</div>
<div class="abs card" style="left:860px">
  <span class="card-icon" style="background:#1ea0dc"></span>
  <svg class="abs" style="left:102px;top:58px" width="36" height="38" viewBox="0 0 36 38"><rect x="2" y="2" width="24" height="32" fill="none" stroke="#fff" stroke-width="3"/><line x1="8" y1="12" x2="20" y2="12" stroke="#fff" stroke-width="2"/><line x1="8" y1="19" x2="20" y2="19" stroke="#fff" stroke-width="2"/><line x1="34" y1="6" x2="20" y2="30" stroke="#fff" stroke-width="4"/></svg>
  <h3>Elementary Tutoring</h3>
  <p>Sed ut perspiciatis unde omnis iste natus error sit voluptatem accusantium doloremque laudantium.</p>
  <div class="more">READ MORE INFO</div>
</div>

<!-- welcome -->
<section class="abs welcome">
  <h2>WELCOME TO BRIGHT PATH MENTORS</h2>
  <p style="top:148px">Maren found her passion for teaching as a high school student. She spent her summer and evenings tutoring the students in her neighborhood. Watching her students grow and succeed by giving them encouragement and specific strategies is what fostered her love of learning. Maren went on to complete her Bachelor of Science from Lakeshore University followed by Teachers College at Rideau Valley University.</p>
  <p style="top:262px">After graduating from her Masters in Education from Rideau Valley University she moved back to Toronto and began working along side a tutoring agency</p>
  <div class="btn">MORE VIDEOS ➜</div>
  <div class="video">
    <div class="video-art" role="img" aria-label="Illustration of a teacher at a chalkboard with two children raising their hands"></div>
    <svg class="abs" style="left:210px;top:112px" width="60" height="60" viewBox="0 0 60 60"><circle cx="30" cy="30" r="28" fill="rgba(0,0,0,.55)" stroke="#fff" stroke-width="2"/><polygon points="24,18 42,30 24,42" fill="#fff"/></svg>
    <div class="video-bar"><span>▶</span><span>00:00/00:03</span><span style="flex:1;height:4px;background:linear-gradient(90deg,var(--orange) 30%,#bbb 30%)"></span><span>◀)</span><span style="width:50px;height:4px;background:var(--orange)"></span></div>
  </div>
</section>

<!-- latest blog -->
<svg class="abs ribbon" style="top:1972px" viewBox="0 0 240 60">
  <polygon points="0,6 34,6 34,40 0,40 12,23" fill="var(--blue)"/>
  <polygon points="240,6 206,6 206,40 240,40 228,23" fill="var(--blue)"/>
  <rect x="24" y="12" width="192" height="40" fill="var(--orange)"/>
</svg>
<div class="abs ribbon-label" style="top:1989px">LATEST BLOG</div>

<article class="abs post" style="left:100px">
  <div class="post-img" role="img" aria-label="Photo of a boy with glasses in front of a back to school chalkboard" style="background:linear-gradient(135deg,#3a5a48,#5e7d62)"></div>
  <h4>Nemo enim ipsam voluptatem</h4>
  <div class="meta">◷ 3 minutes ago, 0 comments</div>
  <p>Lorem ipsum dolor sit amet, consectetur adipiscing elit, sed do eiusmod tempor incididunt ut labore et dolore</p>
</article>
<article class="abs post" style="left:452px">
  <div class="post-img" role="img" aria-label="Photo of children working at computers in a classroom" style="background:linear-gradient(135deg,#e9eef2,#b9c4cc)"></div>
  <h4>Nemo enim ipsam voluptatem</h4>
  <div class="meta">◷ 3 minutes ago, 0 comments</div>
  <p>Lorem ipsum dolor sit amet, consectetur adipiscing elit, sed do eiusmod tempor incididunt ut labore et dolore</p>
</article>
<article class="abs post" style="left:792px">
  <div class="post-img" role="img" aria-label="Photo of smiling schoolchildren at a desk with colored pencils" style="background:linear-gradient(135deg,#6fa9d9,#e7b58a)"></div>
  <h4>Nemo enim ipsam voluptatem</h4>
  <div class="meta">◷ 3 minutes ago, 0 comments</div>
  <p>Lorem ipsum dolor sit amet, consectetur adipiscing elit, sed do eiusmod tempor incididunt ut labore et dolore</p>
</article>

<!-- guarantee -->
<div class="abs guarantee"></div>
<div class="abs seal"></div>
<div class="abs g-big">100%</div>
<div class="abs g-small">SATISFACTION GUARANTEED</div>
<div class="abs sub-input">Enter your E - mail</div>
<div class="abs sub-btn">SUBSCRIBE</div>

<!-- footer -->
<div class="abs footer"></div>
<div class="abs f-title" style="left:97px">QUICK LINKS</div>
<ul class="abs links"><li>Home</li><li>About Us</li><li>Philosophy</li><li>How We Work</li><li>Work With Us</li><li>Blog</li><li>Find A Tutor</li></ul>

<div class="abs f-title" style="left:288px">CONTACTS US</div>
<div class="abs f-contact" style="top:2604px"><svg class="ico" viewBox="0 0 12 12"><path d="M6 0a4 4 0 0 0-4 4c0 3 4 8 4 8s4-5 4-8a4 4 0 0 0-4-4z" fill="#999"/></svg>Bright Path Mentors, Maple Grove<br>Street Riverside.</div>
<div class="abs f-contact" style="top:2658px"><svg class="ico" viewBox="0 0 12 12"><path d="M2 0l2 2-1 2c1 2 2 3 4 4l1-1 2 2-1 3C4 12 0 8 0 2z" fill="#999"/></svg>Phone: +1 555 017 6634</div>
<div class="abs f-contact" style="top:2688px"><svg class="ico" viewBox="0 0 12 12"><rect x="0" y="2" width="12" height="8" fill="#999"/></svg>info@brightpathmentors.ca</div>

<div class="abs f-title" style="left:565px">LATEST TWEET`S</div>
<div class="abs tweet" style="top:2600px"><span class="ico"></span><b>@Bright Path Mentors</b> Fusce susct varius mi. Cum Donec sollicitudin<br><span style="font-size:10px">1 day ago</span></div>
<div class="abs tweet" style="top:2667px"><span class="ico"></span><b>@Bright Path Mentors</b> Fusce susct varius mi. Cum Donec sollicitudin<br><span style="font-size:10px">1 day ago</span></div>

<div class="abs f-brand"><span class="brand-dot"></span><span class="brand-name">Bright Path Mentors</span></div>

<div class="abs bottom">
  <p>©2016 Bright Path Mentors .. All Rights Reserved.</p>
  <div class="soc"><span></span><span></span><span></span><span></span></div>
</div>

</body>
</html>
```